Voranta Imports Busisness cards and logo

Voranta imports is a brand new wholesale company located in Londonderry, New Hampshire dedicated to finding unique products from around the world.
Licensed to sell wine and spirits in the state and also authorized distributors of Pale Meadow Design, a manufacturer of girls and women shoes. Other products that we are currently trying to import are cheese and frozen food from Spain.
We would like a design that portraits our diversity of products and wholesale capabilities

```html
<!DOCTYPE html>
<html lang="en">
<head>
<meta charset="utf-8">
<title>Voranta Imports – Business Cards</title>
<link href="https://fonts.googleapis.com/css2?family=Exo+2:wght@400;500;600&display=swap" rel="stylesheet">
<style>
  :root{
    --page:#e4e4e2;
    --green-dark:#4a8540;
    --green-light:#7ab544;
    --white:#ffffff;
    --card-light:#f4f4f4;
    --card-shade:#d9d9d9;
    --stripe:#8a8a8c;
    --logo-grey:#6d6e71;
    --logo-dot:#5c9e3a;
  }
  *{margin:0;padding:0;box-sizing:border-box}
  html,body{width:1200px;height:900px;overflow:hidden}
  body{background:var(--page);font-family:"Exo 2",sans-serif;position:relative}
  .card{position:absolute;left:240px;width:720px;height:400px;overflow:hidden;
    box-shadow:0 6px 18px rgba(0,0,0,.18)}
  .card-back{top:35px;background:radial-gradient(ellipse at 55% 45%,var(--white) 0%,var(--card-light) 45%,var(--card-shade) 100%)}
  .card-front{top:465px;background:radial-gradient(ellipse at 75% 40%,var(--white) 0%,var(--card-light) 55%,var(--card-shade) 100%)}
  .front-shape{position:absolute;inset:0}
  .brand{position:absolute;display:flex;align-items:center;gap:12px;color:var(--logo-grey);font-weight:600;white-space:nowrap}
  .brand-mark{border-radius:50%;background:var(--logo-dot);flex:none}
  .card-back .brand{left:50%;top:50%;transform:translate(-50%,-50%);font-size:50px}
  .card-back .brand-mark{width:40px;height:40px}
  .card-front .brand{right:34px;top:250px;font-size:30px}
  .card-front .brand-mark{width:26px;height:26px}
  .details{position:absolute;left:44px;top:38px;color:var(--white)}
  .person-name{font-size:25px;font-weight:500;letter-spacing:1.5px;text-transform:uppercase}
  .person-role{font-size:17px;margin-top:2px;letter-spacing:.5px}
  .address{font-size:19px;margin-top:30px;line-height:1.3;letter-spacing:.8px}
  .contacts{list-style:none;margin-top:24px}
  .contacts li{display:flex;align-items:center;gap:12px;font-size:17px;letter-spacing:1.2px;height:28px}
  .contacts svg{width:18px;height:18px;flex:none}
</style>
</head>
<body>

<section class="card card-back" aria-label="Card back">
  <div class="brand"><span class="brand-mark"></span>Voranta Imports</div>
</section>

<section class="card card-front" aria-label="Card front">
  <svg class="front-shape" viewBox="0 0 720 400" preserveAspectRatio="none" aria-hidden="true">
    <defs>
      <linearGradient id="greenFill" x1="0" y1="1" x2="1" y2="0">
        <stop offset="0" stop-color="var(--green-dark)"/>
        <stop offset="1" stop-color="var(--green-light)"/>
      </linearGradient>
    </defs>
    <path d="M388,0 C352,130 372,300 462,400 H476 C386,300 368,130 402,0 Z" fill="var(--stripe)"/>
    <path d="M0,0 H384 C348,130 368,300 458,400 H0 Z" fill="url(#greenFill)"/>
  </svg>

  <div class="details">
    <div class="person-name">Marcus Hollin</div>
    <div class="person-role">Managing Director</div>
    <div class="address">27.4th floor,Harbor<br>Lane Road NHC</div>
    <ul class="contacts">
      <li><svg viewBox="0 0 24 24"><path fill="#fff" d="M6.6 10.8a15 15 0 0 0 6.6 6.6l2.2-2.2a1 1 0 0 1 1-.25 11.4 11.4 0 0 0 3.6.57 1 1 0 0 1 1 1V20a1 1 0 0 1-1 1A17 17 0 0 1 3 4a1 1 0 0 1 1-1h3.5a1 1 0 0 1 1 1c0 1.25.2 2.45.57 3.57a1 1 0 0 1-.25 1z"/></svg>012 345 6789</li>
      <li><svg viewBox="0 0 24 24"><rect x="6" y="2" width="12" height="20" rx="2" fill="none" stroke="#fff" stroke-width="2"/><circle cx="12" cy="18" r="1.2" fill="#fff"/></svg>012 345 6789</li>
      <li><svg viewBox="0 0 24 24"><rect x="3" y="9" width="18" height="11" rx="1.5" fill="#fff"/><rect x="7" y="3" width="10" height="6" fill="none" stroke="#fff" stroke-width="2"/></svg>012 345 6789</li>
      <li><svg viewBox="0 0 24 24"><rect x="2" y="5" width="20" height="14" rx="1.5" fill="none" stroke="#fff" stroke-width="2"/><path d="M2 6l10 7 10-7" fill="none" stroke="#fff" stroke-width="2"/></svg>urname@email.com</li>
      <li><svg viewBox="0 0 24 24"><circle cx="12" cy="12" r="9" fill="none" stroke="#fff" stroke-width="2"/><ellipse cx="12" cy="12" rx="4" ry="9" fill="none" stroke="#fff" stroke-width="1.6"/><path d="M3 12h18M5 7h14M5 17h14" stroke="#fff" stroke-width="1.4"/></svg>www.urwebsitename.com</li>
    </ul>
  </div>

  <div class="brand"><span class="brand-mark"></span>Voranta Imports</div>
</section>

</body>
</html>
```